IT consulting company looking for a modern business design for a website and a new logo

We are the IT-consulting company VelmaTrix from Germany and need a new and modern business website and a new logo. We are specialized in output management. Our services include business analysis, outsourcing, development, training and project leading. We wish for a design with nature pictures (mountains, lakes, rivers, forests, etc.) for our company with the colors green and blue. If it is possible, a slow-mo video of a nature scene. The design should be responsive and the menu should change to a hamburger menu. The following are: • Services / Solutions 1. Output Management 2. Outsourcing 3. Development 4. Business Analyst 5. Training • Partners • Careers • About Us 1. Project A 2. Project B 3. Project C • Contact Notes for the following categories: For "Services / Solutions" we want to conclude some contents from all the sub-points and sub-points below. Additionally, we would like to see some sub-point under "Services / Solutions". For Output Management: "5 Benefits of Output Management Systems (OMS) - OMS Simplifies and Accelerates External Communication - Helps Reduce Communication Mistakes - Provides Customers With Fast and Secure Responses to your questions - Employees can focus on the essential as they can access prepared templates - Companies get complete transparency about their communication "The point" partner does not have sub-points. The content here is a quote and the logo from the company Brel. For now, just placeholders on this site. The next point wants to be "career" without sub-point and wants to contain some text. Carrer options wants to be listed here. Next point wants to be "About us", where we need sub-points which we do not know exactly at this moment, but they will contain text. By clicking directly on "About us" we want to include pictures and texts about 6 employees for which we only need placeholders at the moment. The last point wants to be "contact", where customers can send us messages. The main page should include a story about our company, which can be a placeholder for now. For reference, designs have a look at: https://brelvanto.de/ https://www.tarnopix.com/ https://www.pldrive.de/ We prefer WordPress designs, created with the plugin ELEMENTOR, so that we can easily edit the content by ourselves. The final design should look professional, competent and modern.

Target Market(s)

With our website, we want to reach the following target groups. <br> <br> <br> <br> <br> <br> <br> <br> <br> <br> <br> <br> <br> <br> <br> <br> <br> <br> <br> <br> <br> <br> <br> <br> <br> <br> <br> <br> <br> <br> <br> <br> <br> <br> <br> <br> <br> <br> <br> <br> <br> <br> <br> <br> <br> <br> <br> <br> <br>

Industry/Entity Type

Consulting

Logo Text

(optionally) VelmaTrix

Font styles to use
Sans Serif

Colors

Designer to choose colors to be used in the design.

Requirements
Must have
• 1. Outsourcing 3. Development 4. Business Analyst 5. Training • Partners • Careers • About Us 1. Project A 2. Project B 3. Project C • Contact The above-mentioned background picture with nature motifs (mountains, lakes, rivers, forests, etc.). WordPress design in primary colors blue and green.
Nice to have
• ELEMENTOR template. Effects for the background pictures. Counter of all successful projects for Output Management, Business Analyst and Training

```html
<!DOCTYPE html>
<html lang="en">
<head>
<meta charset="utf-8">
<title>VelmaTrix – IT Consulting</title>
<link href="https://fonts.googleapis.com/css2?family=Lato:wght@400;700;900&family=Open+Sans:wght@400;600;700&display=swap" rel="stylesheet">
<style>
:root{
  --blue:#1c4f9f;
  --blue-dark:#163f82;
  --green:#58ae2f;
  --ink:#222;
  --muted:#6b6b6b;
  --team-bg:#2e3033;
  --white:#fff;
}
*{box-sizing:border-box;margin:0;padding:0}
html,body{width:1200px;height:4368px;overflow:hidden}
body{font-family:"Open Sans",Arial,sans-serif;color:var(--ink);background:var(--white);position:relative}
h1,h2,h3,h4,.brand{font-family:"Lato",Arial,sans-serif}

/* Hero */
.hero{position:relative;height:680px;overflow:hidden}
.hero-photo{position:absolute;inset:0;background:
  radial-gradient(ellipse 260px 120px at 600px 500px,rgba(70,150,170,.9),transparent 75%),
  radial-gradient(ellipse 420px 200px at 160px 560px,rgba(92,150,58,.95),transparent 70%),
  radial-gradient(ellipse 380px 220px at 1080px 520px,rgba(60,110,70,.95),transparent 70%),
  radial-gradient(ellipse 520px 200px at 300px 180px,rgba(120,140,150,.9),transparent 70%),
  radial-gradient(ellipse 520px 220px at 900px 160px,rgba(90,110,110,.9),transparent 70%),
  linear-gradient(180deg,#8ea4b0 0%,#5c7a72 26%,#3f6a58 44%,#3d7f86 62%,#4f8d4a 80%,#34552f 100%)}
.site-nav{position:absolute;top:0;left:0;right:0;height:92px;display:flex;align-items:center;justify-content:space-between;padding:0 112px;background:rgba(0,0,0,.18)}
.brand{color:var(--white);font-weight:900;font-size:42px;letter-spacing:.5px}
.menu{display:flex;gap:30px;list-style:none}
.menu a{color:var(--white);text-decoration:none;font-weight:700;font-size:17px;text-transform:uppercase}
.hero-text{position:absolute;top:226px;left:0;right:0;text-align:center;color:var(--white)}
.hero-text h1{font-size:64px;font-weight:900;text-shadow:0 2px 6px rgba(0,0,0,.35)}
.hero-text p{width:740px;margin:20px auto 0;font-size:20px;font-weight:700;line-height:30px;text-shadow:0 1px 4px rgba(0,0,0,.5)}
.btn{display:inline-flex;align-items:center;gap:8px;background:var(--green);color:var(--white);font-weight:700;font-size:15px;text-transform:uppercase;border-radius:28px;padding:14px 30px;text-decoration:none}
.hero .btn{margin-top:34px}

/* About */
.about{position:relative;height:720px;background:
  radial-gradient(ellipse 500px 260px at 300px 620px,rgba(200,210,220,.35),transparent 70%),
  linear-gradient(180deg,#fff 0%,#f1f3f5 100%)}
.about-copy{position:absolute;left:112px;top:112px;width:500px}
.section-title{font-size:50px;font-weight:900;color:#1c1c1c}
.about-copy p{font-size:15px;line-height:26px;color:var(--muted);margin-top:26px}
.about-copy .btn{margin-top:50px}
.about-photo{position:absolute;left:660px;top:60px;width:330px;height:330px;border-radius:50%;border:12px solid var(--blue);background:
  radial-gradient(circle at 60% 35%,#e9d7c3 0 14%,transparent 30%),
  radial-gradient(ellipse at 55% 75%,#3e6fa6 0 28%,transparent 50%),
  linear-gradient(135deg,#eef2f5 0%,#c9d4dd 40%,#9fb0bf 70%,#6f7f8e 100%)}

/* Services */
.services{height:680px;text-align:center;padding-top:80px;background:linear-gradient(180deg,#fff,#f6f8fa)}
.services .intro{width:880px;margin:22px auto 0;font-size:15px;line-height:26px;color:var(--muted)}
.service-row{display:flex;justify-content:center;align-items:center;gap:70px;margin-top:64px}
.service{width:272px;height:272px;border-radius:50%;background:var(--blue);color:var(--white);display:flex;flex-direction:column;align-items:center;justify-content:center;padding:0 40px}
.service.featured{width:336px;height:336px;background:var(--green);box-shadow:0 0 0 10px #fff,0 0 0 16px var(--green)}
.service svg{width:70px;height:70px;margin-bottom:18px}
.service h3{font-size:22px;font-weight:700;text-transform:uppercase}
.service p{font-size:13px;line-height:20px;margin-top:8px}

/* Team */
.team{height:1120px;color:var(--white);padding-top:100px;background:
  radial-gradient(ellipse 300px 260px at 950px 120px,rgba(120,124,130,.45),transparent 70%),
  radial-gradient(ellipse 300px 240px at 160px 150px,rgba(110,114,120,.35),transparent 70%),
  linear-gradient(180deg,#3a3d41 0%,#2e3033 40%,#34373b 100%)}
.team .section-title{color:var(--white);text-align:center}
.team-grid{display:grid;grid-template-columns:repeat(3,290px);justify-content:center;column-gap:48px;row-gap:46px;margin-top:60px}
.member-photo{position:relative;height:196px;background:
  radial-gradient(ellipse 60px 70px at 50% 38%,#d9c2aa,transparent 80%),
  radial-gradient(ellipse 110px 90px at 50% 100%,#2d3440 0 60%,transparent 80%),
  linear-gradient(135deg,#e4e7ea 0%,#b9bfc6 45%,#8b949e 100%)}
.member-photo.warm{background:
  radial-gradient(ellipse 60px 70px at 50% 38%,#dcc4aa,transparent 80%),
  radial-gradient(ellipse 110px 90px at 50% 100%,#3a3f48 0 60%,transparent 80%),
  linear-gradient(135deg,#e9dcc8 0%,#c8b496 45%,#8e7c64 100%)}
.role{position:absolute;left:0;bottom:0;background:var(--blue);font-weight:700;font-size:16px;text-transform:uppercase;padding:10px 20px}
.member h4{font-size:20px;font-weight:900;text-transform:uppercase;margin-top:28px}
.member p{font-size:12.5px;line-height:20px;color:#c7c9cc;margin-top:14px}
.socials{display:flex;gap:14px;margin-top:18px}
.socials svg{width:18px;height:18px}

/* Partners */
.partners{height:720px;text-align:center;padding-top:120px;background:linear-gradient(180deg,#fff,#f1f3f6)}
.partners .intro{width:900px;margin:22px auto 0;font-size:15px;line-height:26px;color:var(--muted)}
.partner-grid{display:grid;grid-template-columns:repeat(5,180px);gap:24px;justify-content:center;margin-top:64px}
.partner{height:80px;background:var(--white);box-shadow:0 2px 8px rgba(0,0,0,.12);display:flex;align-items:center;justify-content:center;gap:8px;font-family:"Lato",Arial,sans-serif;font-weight:900;font-size:20px;color:var(--blue)}
.partner i{width:14px;height:14px;background:var(--blue);display:block}

/* Footer */
.site-footer{height:448px;background:var(--blue);color:var(--white);position:relative}
.footer-cols{position:absolute;top:100px;left:112px;right:112px;display:grid;grid-template-columns:188px 230px 300px 1fr}
.site-footer h4{font-size:16px;font-weight:900;text-transform:uppercase;margin-bottom:20px}
.site-footer ul{list-style:none}
.site-footer li{font-size:14px;line-height:26px}
.site-footer li::before{content:"›";margin-right:10px;color:var(--green);font-weight:700}
.contact-line{display:flex;gap:12px;align-items:flex-start;font-size:14px;line-height:22px;margin-bottom:16px}
.contact-line svg{flex:none;width:18px;height:18px;margin-top:2px}
.newsletter p{font-size:14px;line-height:22px}
.email-field{margin-top:14px;height:40px;width:250px;border:1px solid rgba(255,255,255,.6);font-size:13px;padding:10px 12px;color:rgba(255,255,255,.8)}
.newsletter .btn{margin-top:14px;padding:10px 24px;font-size:13px}
.footer-social{position:absolute;top:340px;left:0;right:0;display:flex;justify-content:center;gap:12px}
.footer-social span{width:34px;height:34px;border-radius:50%;border:2px solid var(--white);display:flex;align-items:center;justify-content:center}
.footer-social svg{width:16px;height:16px}
.copyright{position:absolute;bottom:0;left:0;right:0;height:60px;display:flex;align-items:center;justify-content:center;font-size:14px;background:var(--blue-dark)}
</style>
</head>
<body>

<header class="hero">
  <div class="hero-photo" role="img" aria-label="Mountain lake landscape with green valleys and a small village"></div>
  <nav class="site-nav">
    <div class="brand">VelmaTrix</div>
    <ul class="menu">
      <li><a href="#">Home</a></li>
      <li><a href="#">About Us</a></li>
      <li><a href="#">Services</a></li>
      <li><a href="#">Partner</a></li>
      <li><a href="#">Careers</a></li>
      <li><a href="#">Contact</a></li>
    </ul>
  </nav>
  <div class="hero-text">
    <h1>VelmaTrix</h1>
    <p>Lorem ipsum dolor sit amet, consectetur adipiscing elit sed do labore et eiusmod tempor incididunt ut labore et dolore magna aliqua.</p>
    <a class="btn" href="#">Read More ›</a>
  </div>
</header>

<section class="about">
  <div class="about-copy">
    <h2 class="section-title">About VelmaTrix</h2>
    <p>Lorem ipsum dolor sit amet, consectetur adipiscing elit, sed do eiusmod tempor incididunt ut labore et dolore magna aliqua.</p>
    <p>Ut enim ad minim veniam, quis nostrud exercitation ullamco laboris nisi ut aliquip ex ea commodo consequat. Duis aute irure dolor in reprehenderit in voluptate velit esse cillum dolore eu fugiat nulla pariatur. Excepteur sint occaecat cupidatat non proident, sunt in culpa qui officia deserunt mollit anim id est laborum.</p>
    <a class="btn" href="#">Read More ›</a>
  </div>
  <div class="about-photo" role="img" aria-label="Consultant working at a desk in a bright office"></div>
</section>

<section class="services">
  <h2 class="section-title">Our Services</h2>
  <p class="intro">Lorem ipsum dolor sit amet, consectetur adipiscing elit do eiusmod tempor incididunt ut labore et dolore magna aliqua. Ut enim ad minim veniam, quis nostrud exercitation ullamco laboris nisi.</p>
  <div class="service-row">
    <div class="service">
      <svg viewBox="0 0 70 70" fill="none" stroke="#fff" stroke-width="3"><circle cx="35" cy="35" r="10"/><circle cx="12" cy="14" r="5"/><circle cx="58" cy="14" r="5"/><circle cx="12" cy="56" r="5"/><circle cx="58" cy="56" r="5"/><path d="M16 18l12 10M54 18L42 28M16 52l12-10M54 52L42 42"/></svg>
      <h3>Outsourcing</h3>
      <p>Lorem ipsum dolor sit amet consectetur adipiscing</p>
    </div>
    <div class="service featured">
      <svg viewBox="0 0 70 70" fill="none" stroke="#fff" stroke-width="3"><rect x="8" y="12" width="54" height="38" rx="3"/><path d="M26 58h18M35 50v8M28 26l-6 5 6 5M42 26l6 5-6 5"/></svg>
      <h3>Development</h3>
      <p>Lorem ipsum dolor sit amet consectetur adipiscing</p>
    </div>
    <div class="service">
      <svg viewBox="0 0 70 70" fill="none" stroke="#fff" stroke-width="3"><rect x="10" y="10" width="50" height="34" rx="2"/><circle cx="35" cy="54" r="6"/><path d="M24 66c2-6 20-6 22 0M20 24h22M20 32h14"/></svg>
      <h3>Trainings</h3>
      <p>Lorem ipsum dolor sit amet consectetur adipiscing</p>
    </div>
  </div>
</section>

<section class="team">
  <h2 class="section-title">Our Team</h2>
  <div class="team-grid">
    <article class="member">
      <div class="member-photo" role="img" aria-label="Portrait of the founder in a suit"><span class="role">The Funder</span></div>
      <h4>Teran Oswick</h4>
      <p>Lorem ipsum dolor sit amet, consectetur adipiscing elit, sed do eiusmod tempor incididunt ut labore et dolore.</p>
      <div class="socials">
        <svg viewBox="0 0 18 18" fill="none" stroke="#58ae2f" stroke-width="2"><rect x="1.5" y="3.5" width="15" height="11"/><path d="M1.5 4l7.5 6 7.5-6"/></svg>
        <svg viewBox="0 0 18 18" fill="#58ae2f"><path d="M4 1l3 4-2 2c1 2 3 4 5 5l2-2 4 3-2 3C8 16 2 10 1 4z"/></svg>
        <svg viewBox="0 0 18 18" fill="none" stroke="#58ae2f" stroke-width="2"><path d="M7.5 10.5l3-3M6 8l-2 2a2.8 2.8 0 004 4l2-2M12 10l2-2a2.8 2.8 0 00-4-4L8 6"/></svg>
      </div>
    </article>
    <article class="member">
      <div class="member-photo warm" role="img" aria-label="Portrait of the chairman in an office"><span class="role">Cherman</span></div>
      <h4>Melisande Virk</h4>
      <p>Lorem ipsum dolor sit amet, consectetur adipiscing elit, sed do eiusmod tempor incididunt ut labore et dolore.</p>
      <div class="socials">
        <svg viewBox="0 0 18 18" fill="none" stroke="#58ae2f" stroke-width="2"><rect x="1.5" y="3.5" width="15" height="11"/><path d="M1.5 4l7.5 6 7.5-6"/></svg>
        <svg viewBox="0 0 18 18" fill="#58ae2f"><path d="M4 1l3 4-2 2c1 2 3 4 5 5l2-2 4 3-2 3C8 16 2 10 1 4z"/></svg>
        <svg viewBox="0 0 18 18" fill="none" stroke="#58ae2f" stroke-width="2"><path d="M7.5 10.5l3-3M6 8l-2 2a2.8 2.8 0 004 4l2-2M12 10l2-2a2.8 2.8 0 00-4-4L8 6"/></svg>
      </div>
    </article>
    <article class="member">
      <div class="member-photo" role="img" aria-label="Portrait of the manager in a suit"><span class="role">As Manager</span></div>
      <h4>Halden Pruss</h4>
      <p>Lorem ipsum dolor sit amet, consectetur adipiscing elit, sed do eiusmod tempor incididunt ut labore et dolore.</p>
      <div class="socials">
        <svg viewBox="0 0 18 18" fill="none" stroke="#58ae2f" stroke-width="2"><rect x="1.5" y="3.5" width="15" height="11"/><path d="M1.5 4l7.5 6 7.5-6"/></svg>
        <svg viewBox="0 0 18 18" fill="#58ae2f"><path d="M4 1l3 4-2 2c1 2 3 4 5 5l2-2 4 3-2 3C8 16 2 10 1 4z"/></svg>
        <svg viewBox="0 0 18 18" fill="none" stroke="#58ae2f" stroke-width="2"><path d="M7.5 10.5l3-3M6 8l-2 2a2.8 2.8 0 004 4l2-2M12 10l2-2a2.8 2.8 0 00-4-4L8 6"/></svg>
      </div>
    </article>
    <article class="member">
      <div class="member-photo warm" role="img" aria-label="Portrait of the co-manager"><span class="role">Co Manager</span></div>
      <h4>Corra Dunvey</h4>
      <p>Lorem ipsum dolor sit amet, consectetur adipiscing elit, sed do eiusmod tempor incididunt ut labore et dolore.</p>
      <div class="socials">
        <svg viewBox="0 0 18 18" fill="none" stroke="#58ae2f" stroke-width="2"><rect x="1.5" y="3.5" width="15" height="11"/><path d="M1.5 4l7.5 6 7.5-6"/></svg>
        <svg viewBox="0 0 18 18" fill="#58ae2f"><path d="M4 1l3 4-2 2c1 2 3 4 5 5l2-2 4 3-2 3C8 16 2 10 1 4z"/></svg>
        <svg viewBox="0 0 18 18" fill="none" stroke="#58ae2f" stroke-width="2"><path d="M7.5 10.5l3-3M6 8l-2 2a2.8 2.8 0 004 4l2-2M12 10l2-2a2.8 2.8 0 00-4-4L8 6"/></svg>
      </div>
    </article>
    <article class="member">
      <div class="member-photo" role="img" aria-label="Portrait of the co-ordinator"><span class="role">Co-Ordinator</span></div>
      <h4>Belric Amont</h4>
      <p>Lorem ipsum dolor sit amet, consectetur adipiscing elit, sed do eiusmod tempor incididunt ut labore et dolore.</p>
      <div class="socials">
        <svg viewBox="0 0 18 18" fill="none" stroke="#58ae2f" stroke-width="2"><rect x="1.5" y="3.5" width="15" height="11"/><path d="M1.5 4l7.5 6 7.5-6"/></svg>
        <svg viewBox="0 0 18 18" fill="#58ae2f"><path d="M4 1l3 4-2 2c1 2 3 4 5 5l2-2 4 3-2 3C8 16 2 10 1 4z"/></svg>
        <svg viewBox="0 0 18 18" fill="none" stroke="#58ae2f" stroke-width="2"><path d="M7.5 10.5l3-3M6 8l-2 2a2.8 2.8 0 004 4l2-2M12 10l2-2a2.8 2.8 0 00-4-4L8 6"/></svg>
      </div>
    </article>
    <article class="member">
      <div class="member-photo" role="img" aria-label="Portrait of the manager"><span class="role">Manager</span></div>
      <h4>Jessa Lindqvar</h4>
      <p>Lorem ipsum dolor sit amet, consectetur adipiscing elit, sed do eiusmod tempor incididunt ut labore et dolore.</p>
      <div class="socials">
        <svg viewBox="0 0 18 18" fill="none" stroke="#58ae2f" stroke-width="2"><rect x="1.5" y="3.5" width="15" height="11"/><path d="M1.5 4l7.5 6 7.5-6"/></svg>
        <svg viewBox="0 0 18 18" fill="#58ae2f"><path d="M4 1l3 4-2 2c1 2 3 4 5 5l2-2 4 3-2 3C8 16 2 10 1 4z"/></svg>
        <svg viewBox="0 0 18 18" fill="none" stroke="#58ae2f" stroke-width="2"><path d="M7.5 10.5l3-3M6 8l-2 2a2.8 2.8 0 004 4l2-2M12 10l2-2a2.8 2.8 0 00-4-4L8 6"/></svg>
      </div>
    </article>
  </div>
</section>

<section class="partners">
  <h2 class="section-title">Our Partners</h2>
  <p class="intro">Lorem ipsum dolor sit amet, consectetur adipiscing elit do eiusmod tempor incididunt ut labore et dolore magna aliqua. Ut enim ad minim veniam, quis nostrud exercitation ullamco.</p>
  <div class="partner-grid">
    <div class="partner"><i></i>Orvanta</div>
    <div class="partner">Kelvora</div>
    <div class="partner">Banca Ferrelli</div>
    <div class="partner">Solvane</div>
    <div class="partner"><i></i>Drumo</div>
    <div class="partner">Veyrant Life</div>
    <div class="partner"><i></i>Quorvel</div>
    <div class="partner">Halbrook</div>
    <div class="partner">Maison Treval</div>
    <div class="partner"><i></i>Lanzi Bank</div>
    <div class="partner">Northmere</div>
    <div class="partner">Taskor</div>
    <div class="partner">Pravix</div>
    <div class="partner">Lumetra</div>
    <div class="partner"><i></i>Ardenso</div>
  </div>
</section>

<footer class="site-footer">
  <div class="footer-cols">
    <div>
      <h4>Quick Links</h4>
      <ul><li>Home</li><li>About Us</li><li>Services</li><li>Partners</li><li>Location</li></ul>
    </div>
    <div>
      <h4>Other Links</h4>
      <ul><li>Services</li><li>Help</li><li>Terms &amp; Conditions</li><li>FAQs</li><li>Contact Us</li></ul>
    </div>
    <div>
      <h4>Contact Us</h4>
      <div class="contact-line"><svg viewBox="0 0 18 18" fill="#fff"><path d="M9 1a6 6 0 00-6 6c0 4.5 6 10 6 10s6-5.5 6-10a6 6 0 00-6-6zm0 8.2A2.2 2.2 0 119 4.8a2.2 2.2 0 010 4.4z"/></svg><span>48 Lindenweg, Aldorf<br>10115</span></div>
      <div class="contact-line"><svg viewBox="0 0 18 18" fill="#fff"><path d="M4 1l3 4-2 2c1 2 3 4 5 5l2-2 4 3-2 3C8 16 2 10 1 4z"/></svg><span>(+49) 301 555 0192</span></div>
      <div class="contact-line"><svg viewBox="0 0 18 18" fill="none" stroke="#fff" stroke-width="1.6"><rect x="1.5" y="3.5" width="15" height="11"/><path d="M1.5 4l7.5 6 7.5-6"/></svg><span>info@velmatrix.com</span></div>
    </div>
    <div class="newsletter">
      <h4>Newsletter Subscription</h4>
      <p>Register your Email address to get more information about us.</p>
      <div class="email-field">Email Address</div>
      <a class="btn" href="#">Subscribe</a>
    </div>
  </div>
  <div class="footer-social">
    <span><svg viewBox="0 0 18 18" fill="none" stroke="#fff" stroke-width="1.8"><rect x="1.5" y="3.5" width="15" height="11"/><path d="M1.5 4l7.5 6 7.5-6"/></svg></span>
    <span><svg viewBox="0 0 18 18" fill="#fff"><path d="M4 1l3 4-2 2c1 2 3 4 5 5l2-2 4 3-2 3C8 16 2 10 1 4z"/></svg></span>
    <span><svg viewBox="0 0 18 18" fill="none" stroke="#fff" stroke-width="1.8"><path d="M7.5 10.5l3-3M6 8l-2 2a2.8 2.8 0 004 4l2-2M12 10l2-2a2.8 2.8 0 00-4-4L8 6"/></svg></span>
    <span><svg viewBox="0 0 18 18" fill="#fff"><path d="M9 1a6 6 0 00-6 6c0 4.5 6 10 6 10s6-5.5 6-10a6 6 0 00-6-6zm0 8.2A2.2 2.2 0 119 4.8a2.2 2.2 0 010 4.4z"/></svg></span>
  </div>
  <div class="copyright">Copyrights © 2019 VelmaTrix. All Rights Reserved &nbsp;|&nbsp; Privacy Policy</div>
</footer>

</body>
</html>
```